International Clinical Software Company needs a new business card design

We are looking for a new business card design for our company that has recently expanded into the UK market, making us a multinational company.
After having rebranded our website and produced a new style guide, we are looking for a business card that is creative and attention grabbing, while being consistent with the style and colour scheme used on the new website, www.plumvora.example
We produce care management technology for the aged care market, but the main aspect we aim to communicate is the human element of our software, and the way it assists in providing better care for aged people, and stronger relationships between aged people and the staff that care for them.
Our current business card is a dark green with gold text, which makes the text quite difficult to read, not very aesthetically appealing and the colour scheme looks quite dated.
We would like something fresh and modern, that can still be colourful but doesn't use large blocks of dark colour, and uses the colours within our logo.
Something tying in with the leaves that are used in our logo could work quite nicely, along with the Autumn/Fall colours of soft greens, yellows and reds (also in our existing logo). However also happy to look at fresh, completely out of the box ideas we may not have yet considered.
Target Market(s)
The people that receive this business card work in the aged card or health industry and are either corporate/management level staff or clinical (Registered Nurses, care workers etc.)
Industry/Entity Type
Health Product
Contact Information for Business Card
Company Name - BrindlewayCare
Company locations: United Kingdom, Australia, New Zealand
Staff Details:
Staff name: Derek Mallow
Staff job title: Executive Chairman
Staff email: d.mallow@plumvora.example
Office phone number: 01742 918576
Font styles to use
Other font styles liked:
- Calibri
Requirements
Must have
- Must include the BrindlewayCare brand name in it's current font
- Must include logo (3 leaves in gold circle)
- Must include Business Card Details
Nice to have
- Elements of gold
- White space
- Something autumn themed but not too cliched
Should not have
- No blue - used by a major competitor and we would like to differentiate from them
- Large blocks of dark green colour (the green that appears in our leaves on the logo on our current business card is the background colour and it is far too dark)

```html
<!DOCTYPE html>
<html lang="en">
<head>
<meta charset="utf-8">
<title>BrindlewayCare Business Card</title>
<link rel="stylesheet" href="https://fonts.googleapis.com/css2?family=Open+Sans:wght@400;600;700&display=swap">
<style>
  :root {
    --backdrop: #3b3431;
    --card: #f6f2ea;
    --card-edge: #e2dacb;
    --gold: #b0945a;
    --gold-deep: #9a7f46;
    --text-main: #3a3430;
    --faint: #e6dece;
  }
  * { box-sizing: border-box; margin: 0; padding: 0; }
  html, body {
    width: 1200px;
    height: 900px;
    overflow: hidden;
    background: var(--backdrop);
    font-family: "Open Sans", Calibri, Arial, sans-serif;
  }
  .canvas {
    width: 1200px;
    height: 900px;
    display: flex;
    align-items: center;
    justify-content: center;
    gap: 60px;
  }
  .card {
    position: relative;
    width: 525px;
    height: 300px;
    background: var(--card);
    border: 1px solid var(--card-edge);
    box-shadow: 0 14px 30px rgba(0, 0, 0, 0.45);
    overflow: hidden;
  }

  /* Front: contact side */
  .brand-block {
    position: absolute;
    left: 0;
    top: 0;
    width: 262px;
    height: 300px;
    display: flex;
    flex-direction: column;
    align-items: center;
    justify-content: center;
    gap: 18px;
  }
  .brand-mark {
    width: 78px;
    height: 78px;
    border-radius: 50%;
    background: var(--gold);
  }
  .brand-name {
    color: var(--gold);
    font-weight: 400;
    font-size: 28px;
    letter-spacing: 0.5px;
  }
  .divider {
    position: absolute;
    left: 262px;
    top: 50px;
    width: 1px;
    height: 200px;
    background: linear-gradient(to bottom, transparent, var(--gold-deep) 30%, var(--gold-deep) 70%, transparent);
  }
  .contact {
    position: absolute;
    left: 288px;
    top: 62px;
    color: var(--text-main);
    font-size: 14px;
    line-height: 1.35;
  }
  .contact-name {
    color: var(--gold);
    font-weight: 700;
    font-size: 17px;
  }
  .contact-title { margin-bottom: 14px; }
  .contact-phone {
    display: flex;
    align-items: center;
    gap: 8px;
    font-size: 13px;
  }
  .contact-email {
    margin-bottom: 14px;
    padding-left: 20px;
    font-size: 13px;
  }
  .icon-phone { width: 12px; height: 12px; fill: var(--gold); }

  /* Back: brand side */
  .card-back {
    display: flex;
    align-items: center;
    justify-content: center;
  }
  .faint-circle {
    position: absolute;
    left: 50%;
    top: 50%;
    width: 230px;
    height: 230px;
    margin: -115px 0 0 -115px;
    border-radius: 50%;
    border: 4px solid var(--faint);
  }
  .back-name {
    position: relative;
    color: var(--gold);
    font-weight: 400;
    font-size: 46px;
    letter-spacing: 0.5px;
  }
</style>
</head>
<body>
<main class="canvas">
  <section class="card card-front" aria-label="Business card front">
    <div class="brand-block">
      <div class="brand-mark"></div>
      <div class="brand-name">BrindlewayCare</div>
    </div>
    <div class="divider"></div>
    <div class="contact">
      <p class="contact-name">Derek Mallow</p>
      <p class="contact-title">Executive Chairman</p>
      <p class="contact-phone">
        <svg class="icon-phone" viewBox="0 0 24 24" aria-hidden="true">
          <path d="M6.6 10.8c1.4 2.8 3.8 5.1 6.6 6.6l2.2-2.2c.3-.3.7-.4 1-.2 1.1.4 2.3.6 3.6.6.6 0 1 .4 1 1V20c0 .6-.4 1-1 1C10.6 21 3 13.4 3 4c0-.6.4-1 1-1h3.5c.6 0 1 .4 1 1 0 1.3.2 2.5.6 3.6.1.3 0 .7-.2 1l-2.3 2.2z"/>
        </svg>
        01742 918576
      </p>
      <p class="contact-email">d.mallow@plumvora.example</p>
      <p class="contact-locations">United Kingdom, Australia<br>New Zealand</p>
    </div>
  </section>

  <section class="card card-back" aria-label="Business card back">
    <div class="faint-circle"></div>
    <div class="back-name">BrindlewayCare</div>
  </section>
</main>
</body>
</html>
```